Evaporative Air Conditioning Summer Service

Would like to design a flyer to send out in an email to existing clients to promote a Pre-summer service for Evaporative Air Conditioners
Cost will be $110.00 inc gst
Tasks included in service are
- Inspection and clean of pads
- Inspection and check float valve, water pump, fan, motor, bearings, drain
- Clean basin
- Supply of bacterial tablet
- Inspect overall condition of unit
- Any repairs if required will be quoted
Please see files attached of a previous very basic flyer I have used for installation and replacement unit costs. This has current contact information
Have also uploaded company logo for use.
Thanks
Plumbing

```html
<!DOCTYPE html>
<html lang="en">
<head>
<meta charset="utf-8">
<title>Summit Gas &amp; Plumbing – Evaporative Air Con Summer Service</title>
<link rel="stylesheet" href="https://fonts.googleapis.com/css2?family=Barlow:wght@500;600&family=Poppins:wght@500;600;700&display=swap">
<style>
  :root {
    --orange: #e2622c;
    --orange-soft: #e87a45;
    --blue: #1b75bb;
    --ink: #151515;
    --paper: #f4f4f4;
    --backdrop: #e6e7e9;
    --white: #ffffff;
    --grey-photo: #5b6462;
  }
  * { box-sizing: border-box; margin: 0; padding: 0; }
  html, body {
    width: 1200px; height: 1006px; overflow: hidden;
    background: var(--backdrop);
  }
  .flyer {
    position: absolute; left: 257px; top: 22px;
    width: 686px; height: 962px;
    background: var(--paper);
    overflow: hidden;
    font-family: "Poppins", sans-serif;
    box-shadow: 0 2px 10px rgba(0,0,0,.12);
  }
  .abs { position: absolute; }

  /* brand */
  .brand { left: 31px; top: 50px; display: flex; align-items: center; gap: 10px; }
  .brand-dot { width: 40px; height: 40px; border-radius: 50%; background: var(--blue); }
  .brand-name {
    font-family: "Poppins", sans-serif; font-weight: 700; font-size: 25px;
    color: var(--blue); letter-spacing: .5px; line-height: 1;
  }

  /* headline */
  .headline-dark {
    left: 25px; top: 146px; font-family: "Barlow", sans-serif; font-weight: 600;
    font-size: 40px; color: var(--ink); letter-spacing: .5px; line-height: 1;
  }
  .headline-tag {
    left: 21px; height: 40px; padding: 0 5px; background: var(--blue);
    font-family: "Barlow", sans-serif; font-weight: 500; font-size: 37px;
    color: var(--white); line-height: 40px; letter-spacing: .5px;
  }
  .tag-supply { top: 191px; }
  .tag-install { top: 239px; }
  .price {
    left: 22px; top: 288px; font-weight: 700; font-size: 60px;
    color: var(--orange); line-height: 1; letter-spacing: -1px;
  }
  .price-note {
    left: 23px; top: 350px; font-weight: 700; font-size: 32px;
    color: var(--blue); line-height: 1;
  }

  .unit-photo {
    left: 390px; top: 125px; width: 296px; height: 228px;
    border-radius: 14px 0 0 14px;
    background: linear-gradient(180deg, #6b7371 0%, var(--grey-photo) 55%, #3f4645 100%);
  }

  /* service band */
  .service-band {
    left: 0; top: 403px; width: 686px; height: 312px;
    background: var(--orange-soft);
  }
  .service-tab { left: 176px; top: 392px; }
  .service-tab-label {
    left: 176px; top: 392px; width: 335px; height: 38px;
    text-align: center; line-height: 40px; font-weight: 600; font-size: 21px;
    color: var(--white);
  }
  .service-list { left: 20px; top: 437px; list-style: none; }
  .service-list li {
    position: relative; padding-left: 30px; color: var(--white);
    font-weight: 500; font-size: 19.5px; line-height: 37.5px;
  }
  .service-list li::before {
    content: ""; position: absolute; left: 0; top: 12px;
    width: 14px; height: 14px; background: var(--white);
  }
  .service-list li.wrap { line-height: 37px; }
  .service-list li.gap { margin-top: 6px; }
  .service-photos {
    left: 455px; top: 425px; width: 231px; height: 290px;
    background: linear-gradient(160deg, #c9ccd0 0%, #7c8690 45%, var(--blue) 100%);
    border-radius: 40px 0 0 0;
  }

  .divider {
    left: 21px; top: 715px; width: 544px; height: 9px;
    border-radius: 5px; background: var(--blue);
  }

  /* repairs */
  .repairs {
    left: 28px; top: 742px; font-weight: 600; font-size: 31px; line-height: 38px;
    letter-spacing: .3px;
  }
  .repairs .accent { color: var(--orange); display: block; }
  .repairs .strong { color: var(--blue); display: block; }
  .pump-photo {
    left: 450px; top: 736px; width: 212px; height: 132px; border-radius: 10px;
    background: linear-gradient(135deg, #5fb3e6 0%, #2f8fd0 60%, #1d6fa9 100%);
  }

  /* contact */
  .contact-band {
    left: 0; top: 885px; width: 686px; height: 77px; background: var(--orange);
  }
  .phone-tab { left: 176px; top: 872px; }
  .phone {
    left: 176px; top: 872px; width: 335px; height: 38px; text-align: center;
    line-height: 40px; font-weight: 600; font-size: 30px; letter-spacing: 4px;
    color: var(--white);
  }
  .email {
    left: 0; top: 914px; width: 686px; text-align: center;
    font-weight: 500; font-size: 18px; color: var(--white);
  }
</style>
</head>
<body>
<main class="flyer">

  <div class="abs brand">
    <span class="brand-dot"></span>
    <span class="brand-name">SUMMIT GAS &amp; PLUMBING</span>
  </div>

  <h1 class="abs headline-dark">AIR CON REPAIR</h1>
  <div class="abs headline-tag tag-supply">SUPPLY AND</div>
  <div class="abs headline-tag tag-install">INSTALLATION</div>
  <div class="abs price">$110.00</div>
  <div class="abs price-note">INC GST</div>

  <div class="abs unit-photo" role="img" aria-label="Photo of a grey evaporative air conditioning roof unit"></div>

  <section class="abs service-band"></section>
  <div class="abs service-photos" role="img" aria-label="Photos of fan bearings and outdoor air conditioning condenser units"></div>
  <svg class="abs service-tab" width="335" height="38" viewBox="0 0 335 38" aria-hidden="true">
    <polygon points="0,0 335,0 312,38 23,38" fill="var(--blue)"/>
  </svg>
  <div class="abs service-tab-label">SERVICE ARE</div>

  <ul class="abs service-list">
    <li>Inspection and clean of pads</li>
    <li class="wrap">Inspection and check float valve,<br>water pump, fan, motor, bearings, drain</li>
    <li>Clean basin</li>
    <li class="gap">Supply of bacterial tablet</li>
    <li>Inspect overall condition of unit</li>
    <li>Any repairs if required will be quoted</li>
  </ul>

  <div class="abs divider"></div>

  <p class="abs repairs">
    <span class="accent">FAULT FINDING AND</span>
    <span class="accent">REPAIRS AS PER</span>
    <span class="strong">NORMAL HOURLY RATE</span>
  </p>
  <div class="abs pump-photo" role="img" aria-label="Photo of a blue industrial water pump and motor"></div>

  <footer>
    <div class="abs contact-band"></div>
    <svg class="abs phone-tab" width="335" height="38" viewBox="0 0 335 38" aria-hidden="true">
      <polygon points="0,0 335,0 312,38 23,38" fill="var(--blue)"/>
    </svg>
    <div class="abs phone">041 5550 182</div>
    <div class="abs email">admin@summitgasandplumbing.com.au</div>
  </footer>

</main>
</body>
</html>
```